Website for Excavator and Earthworks Company

We require a modern, sleek and practical website for our newly created earthworks/excavator business in Perth, Western Australia called Bluegum Ridge Earthworks.

The website should have a modern, cutting edge feel but only needs to be relatively simplistic in it's layout and eventual functionality.

Some pages it should have would be Home, About, Projects and Contact Us.

```html
<!DOCTYPE html>
<html lang="en">
<head>
<meta charset="utf-8">
<title>Bluegum Ridge Earthworks</title>
<link href="https://fonts.googleapis.com/css2?family=Archivo:wght@400;500;600;700&family=Michroma&family=Oswald:wght@600;700&display=swap" rel="stylesheet">
<style>
:root{
  --lime:#c6cf2e;
  --lime-dark:#aab521;
  --amber:#d9951c;
  --ink:#161616;
  --charcoal:#2b2b2b;
  --text:#2a2a2a;
  --muted:#6b6b6b;
  --white:#ffffff;
  --line:#d9d9d9;
}
*{box-sizing:border-box;margin:0;padding:0}
html,body{width:1200px;height:3734px;overflow:hidden}
body{position:relative;background:var(--white);font-family:"Archivo",Arial,sans-serif;color:var(--text)}
.abs{position:absolute}
.wide{font-family:"Michroma",Arial,sans-serif;font-weight:400;letter-spacing:.5px}
.eyebrow{font-size:15px;color:var(--lime-dark);display:flex;align-items:center;gap:6px}
.eyebrow::before,.eyebrow.both::after{content:"";width:30px;height:2px;background:var(--lime)}
.btn{display:inline-flex;align-items:center;justify-content:center;font-size:13px;font-weight:500;text-decoration:none}
.btn-lime{background:var(--lime);color:var(--ink)}
.btn-dark{background:var(--ink);color:var(--white)}

/* header */
.site-header{left:0;top:0;width:1200px;height:99px;background:var(--white)}
.brand{display:flex;align-items:center;gap:10px;color:var(--ink);font-weight:700}
.brand-mark{width:26px;height:26px;background:var(--lime)}
.brand-name{font-size:15px;line-height:1.1;text-transform:uppercase}
.main-nav{left:403px;top:40px;display:flex;gap:34px;font-size:13px;color:var(--ink)}
.main-nav .active{color:var(--lime-dark)}
.header-call{left:873px;top:0;height:99px;border-left:1px solid var(--line);padding:30px 0 0 22px;display:flex;gap:10px}
.header-call small{display:block;font-size:11px;color:var(--lime-dark)}
.header-call strong{font-size:19px;font-weight:500;color:var(--ink)}

/* hero */
.hero-photo{left:0;top:99px;width:1200px;height:600px;background:linear-gradient(100deg,#3a2a18 0%,#7a5226 35%,#c7862f 60%,#e3a445 75%,#6b4a25 100%)}
.hero-shade{left:0;top:99px;width:700px;height:600px;background:linear-gradient(90deg,rgba(20,14,8,.65),rgba(20,14,8,0))}
.hero-title{left:143px;top:240px;font-family:"Oswald",Arial,sans-serif;font-weight:700;font-size:64px;line-height:66px;color:var(--white);text-transform:uppercase}
.hero-title span{color:var(--lime)}
.hero-copy{left:143px;top:384px;width:470px;font-size:14px;line-height:21px;color:var(--white)}
.hero-actions{left:143px;top:448px;display:flex;gap:8px}
.hero-actions .btn{height:39px;padding:0 16px}

/* about */
.about-photo{left:140px;top:836px;width:498px;height:272px;background:linear-gradient(160deg,#8fb1d8 0%,#e8c68a 45%,#c49a48 70%,#6d5a3c 100%);clip-path:polygon(0 0,58% 0,58% 28%,100% 30%,80% 100%,0 100%)}
.about-text{left:680px;top:770px;width:380px}
.about-text h2{font-size:31px;line-height:40px;color:var(--ink);margin-top:12px}
.about-text h3{font-size:16px;font-weight:500;color:var(--lime-dark);margin:10px 0 14px}
.about-text p{font-size:12.5px;line-height:23px;color:var(--text)}
.about-text .btn{margin-top:30px;height:37px;padding:0 14px}

/* services */
.services-intro{left:0;top:1265px;width:413px;height:600px;background:linear-gradient(180deg,#4a4a48 0%,#3a352c 55%,#5a4a2a 80%,#2a2722 100%)}
.services-intro-text{left:98px;top:1425px;width:260px;color:var(--white)}
.services-intro-text h2{font-size:32px;line-height:40px;margin:8px 0 18px}
.services-intro-text p{font-size:15px;line-height:28px}
.service{width:262px;height:300px;padding:58px 34px 0 35px;color:var(--white)}
.service.amber{background:linear-gradient(180deg,rgba(217,149,28,.92),rgba(200,135,20,.95))}
.service.dark{background:linear-gradient(180deg,#3a3a3a,#262626)}
.service svg{width:52px;height:52px;display:block;margin-bottom:20px}
.service h3{font-size:16px;line-height:20px;font-weight:400}
.service p{font-size:12px;line-height:19px;margin-top:10px}

/* projects */
.projects-head{left:0;top:1958px;width:1200px;text-align:center}
.projects-head .eyebrow{justify-content:center}
.projects-head .eyebrow::after{content:"";width:30px;height:2px;background:var(--lime)}
.projects-head h2{font-size:30px;color:var(--ink);margin-top:12px}
.project{overflow:hidden;color:var(--white);display:flex;flex-direction:column;justify-content:flex-end;padding:0 20px 18px}
.project h3{font-size:14px;line-height:18px;font-weight:400}
.project p{font-size:12px;line-height:17px;margin-top:6px}
.project::after{content:"";position:absolute;inset:0;background:linear-gradient(180deg,rgba(0,0,0,0) 45%,rgba(0,0,0,.7));z-index:0}
.project>*{position:relative;z-index:1}

/* quote */
.quote-bg{left:0;top:2565px;width:1200px;height:530px;background:linear-gradient(180deg,#151515,#2c2c2c 60%,#1d1d1d)}
.quote-head{left:0;top:2652px;width:1200px;text-align:center;color:var(--white)}
.quote-head .eyebrow{justify-content:center}
.quote-head .eyebrow::after{content:"";width:30px;height:2px;background:var(--lime)}
.quote-head h2{font-size:31px;margin:10px 0 12px}
.quote-head p{font-size:14px;line-height:22px}
.quote-card{left:210px;top:2797px;width:780px;height:318px;background:var(--white);box-shadow:0 10px 30px rgba(0,0,0,.18);display:flex}
.quote-form{width:491px;padding:32px 26px 0 26px;display:grid;grid-template-columns:1fr 1fr;column-gap:30px;align-content:start}
.field{font-size:12px;color:var(--ink);border-bottom:1px solid var(--line);padding-bottom:12px;margin-bottom:14px}
.field.full{grid-column:1/3;height:94px}
.quote-form .btn{grid-column:2;justify-self:end;height:37px;width:162px;font-size:15px;font-weight:600}
.contact-info{width:289px;background:var(--lime);padding:30px 46px}
.contact-info h3{font-size:16px;line-height:24px;color:var(--ink);margin-bottom:12px}
.info-row{display:flex;gap:12px;font-size:12px;line-height:18px;color:var(--ink);margin-bottom:14px}
.info-row svg{flex:none;width:26px;height:26px}
.socials{display:flex;gap:9px;margin-top:14px}
.socials span{width:27px;height:27px;border:1.5px solid var(--ink);display:flex;align-items:center;justify-content:center}
.socials span::after{content:"";width:9px;height:9px;background:var(--ink)}

/* newsletter */
.news-art{left:300px;top:3225px;width:118px;height:124px;background:linear-gradient(150deg,#3f6fd0,#1b3a8a);border-radius:6px;transform:rotate(-12deg)}
.news-title{left:413px;top:3215px;width:485px;text-align:center;font-size:17px;color:#1b3a8a}
.news-copy{left:413px;top:3252px;width:485px;text-align:center;font-size:13.5px;line-height:22px}
.news-form{left:413px;top:3310px;width:485px;height:38px;display:flex;border:1px solid var(--line)}
.news-form span{flex:1;font-size:12px;padding:12px 10px}
.news-form strong{width:154px;background:var(--lime);display:flex;align-items:center;justify-content:center;font-family:"Michroma",Arial,sans-serif;font-size:14px;color:var(--ink)}

/* footer */
.footer-rule{left:141px;top:3398px;width:917px;height:1px;background:var(--line)}
.footer-brand{left:0;top:3452px;width:1200px;display:flex;justify-content:center}
.footer-nav{left:352px;top:3545px;display:flex;gap:38px;font-size:13px;color:var(--ink)}
.footer-nav .active{color:var(--lime-dark)}
.footer-bottom{left:0;top:3627px;width:1200px;height:107px;background:var(--ink)}
.footer-bar{left:141px;top:3576px;width:917px;height:90px;background:var(--lime);display:flex;gap:70px;padding:22px 0 0 178px}
.footer-bar .info-row{font-size:12.5px}
.footer-digger{left:930px;top:3450px;width:250px;height:200px;background:linear-gradient(150deg,#f0a63a,#c97b16 55%,#3a3a3a);clip-path:polygon(35% 0,70% 20%,100% 75%,95% 100%,10% 100%,0 70%)}
.copyright{left:143px;top:3693px;font-size:12px;color:var(--white)}
.footer-social{left:905px;top:3683px;display:flex;gap:10px}
.footer-social span{width:30px;height:30px;border:1.5px solid var(--white);display:flex;align-items:center;justify-content:center}
.footer-social span::after{content:"";width:10px;height:10px;background:var(--white)}
</style>
</head>
<body>

<header class="site-header abs">
  <div class="brand abs" style="left:141px;top:30px">
    <span class="brand-mark"></span>
    <span class="brand-name">Bluegum Ridge<br>Earthworks</span>
  </div>
  <nav class="main-nav abs">
    <span class="active">HOME</span><span>ABOUT US</span><span>SERVICES</span><span>PROJECTS</span><span>CONTACT US</span>
  </nav>
  <div class="header-call abs">
    <svg width="28" height="30" viewBox="0 0 28 30" fill="none" stroke="#c6cf2e" stroke-width="2"><path d="M6 3h6l2 7-4 2a16 16 0 0 0 7 7l2-4 7 2v6c0 2-2 4-4 4C11 27 2 18 2 7c0-2 2-4 4-4z"/></svg>
    <div><small>Call Us</small><strong>(123) 456 7890</strong></div>
  </div>
</header>

<section class="hero">
  <div class="hero-photo abs" role="img" aria-label="Excavator digging into dusty earth at golden hour"></div>
  <div class="hero-shade abs"></div>
  <h1 class="hero-title abs">Earth moved<br>with <span>precision</span></h1>
  <p class="hero-copy abs">Professional excavation, bulk earthworks, site preparation and land development services across Perth and Western Australia.</p>
  <div class="hero-actions abs">
    <a class="btn btn-lime">GET A QUOTE TODAY</a>
    <a class="btn btn-dark">VIEW OUR PROJECTS</a>
  </div>
  <svg class="abs" style="left:0;top:590px" width="1200" height="170" viewBox="0 590 1200 170">
    <polygon points="0,690 1200,640 1200,760 0,760" fill="#fff"/>
    <polygon points="795,633 1200,603 1200,670" fill="#c6cf2e"/>
    <polygon points="0,675 300,666 0,753" fill="#161616"/>
  </svg>
</section>

<section class="about">
  <div class="about-photo abs" role="img" aria-label="Excavator on a work site under a sunset sky"></div>
  <div class="about-text abs">
    <div class="eyebrow">ABOUT</div>
    <h2 class="wide">BLUEGUM RIDGE<br>EARTHWORKS</h2>
    <h3>Bluegum Ridge Earthworks: Building Perth's Future</h3>
    <p>Based in Perth, Western Australia, Bluegum Ridge Earthworks is a premier excavation and earthworks company specializing in residential, commercial, and industrial projects.</p>
    <p>With over 15 years of industry experience, our team combines cutting-edge equipment with skilled operators to deliver exceptional results on time and within budget.</p>
    <p>We pride ourselves on our commitment to safety, precision, and environmental responsibility in every project we undertake.</p>
    <a class="btn btn-lime">CONTACT OUR TEAM</a>
  </div>
</section>

<section class="services">
  <div class="services-intro abs" role="img" aria-label="Excavators on a site under a stormy sky"></div>
  <div class="services-intro-text abs">
    <div class="eyebrow">WHAT WE DO</div>
    <h2 class="wide">OUR<br>SERVICES</h2>
    <p>Comprehensive earthmoving and excavation solutions for projects of all sizes across Perth and regional WA.</p>
  </div>
  <div class="service amber abs" style="left:413px;top:1265px">
    <svg viewBox="0 0 52 52" fill="#fff"><rect x="4" y="30" width="28" height="10" rx="5"/><rect x="10" y="20" width="14" height="10"/><path d="M24 22l14-14 8 6-3 3-5-3-12 11z"/></svg>
    <h3 class="wide">Bulk<br>Earthworks</h3>
    <p>Large-scale cut and fill operations, land levelling, and soil compaction for subdivisions and commercial developments.</p>
  </div>
  <div class="service dark abs" style="left:675px;top:1265px">
    <svg viewBox="0 0 52 52" fill="#fff"><rect x="4" y="38" width="44" height="8"/><path d="M20 38l8-16 8 4-6 12z"/><circle cx="34" cy="12" r="5"/></svg>
    <h3 class="wide">Land<br>Clearing</h3>
    <p>Vegetation removal, stump grinding, and site preparation for residential, agricultural and commercial properties.</p>
  </div>
  <div class="service amber abs" style="left:937px;top:1265px">
    <svg viewBox="0 0 52 52" fill="#fff"><path d="M20 4h8l10 40H10z"/><rect x="4" y="44" width="44" height="4"/></svg>
    <h3 class="wide">Road &amp; Driveway<br>Construction</h3>
    <p>Formation, grading and compaction for access roads, farm tracks, and residential driveways.</p>
  </div>
  <div class="service dark abs" style="left:413px;top:1565px">
    <svg viewBox="0 0 52 52" fill="none" stroke="#fff" stroke-width="3"><path d="M6 4h16v42H6zM22 20q10 0 12 12t12 12"/></svg>
    <h3 class="wide">Dam<br>&amp; Drainage</h3>
    <p>Dam construction, excavation, lining, and drainage solutions for flood mitigation and water management.</p>
  </div>
  <div class="service amber abs" style="left:675px;top:1565px">
    <svg viewBox="0 0 52 52" fill="#fff"><rect x="8" y="4" width="4" height="44"/><rect x="4" y="8" width="30" height="4"/><rect x="24" y="26" width="22" height="22"/></svg>
    <h3 class="wide">Site<br>Preparation</h3>
    <p>Complete site preparation for residential and commercial construction, including slab foundations and pad preparation.</p>
  </div>
  <div class="service dark abs" style="left:937px;top:1565px">
    <svg viewBox="0 0 52 52" fill="#fff"><path d="M4 18h30l-4 20H8z"/><circle cx="12" cy="44" r="4"/><circle cx="28" cy="44" r="4"/><circle cx="40" cy="14" r="9" fill="none" stroke="#fff" stroke-width="3"/></svg>
    <h3 class="wide">Material<br>Supply &amp; Removal</h3>
    <p>Supply of quality fill material, sand, gravel, and removal of excess spoil from your site.</p>
  </div>
</section>

<section class="projects">
  <div class="projects-head abs">
    <div class="eyebrow">CREATIONS</div>
    <h2 class="wide">OUR PROJECTS</h2>
  </div>
  <article class="project abs" style="left:141px;top:2062px;width:286px;height:229px;background:linear-gradient(160deg,#b58a5a,#8a6238 50%,#5d4124)" role="img" aria-label="Excavator working in a rocky quarry">
    <h3 class="wide">Lorem ipsum dolorsit</h3>
    <p>Duis autem vel eum iriure dolor in hendrerit in vulputate velit esse mole.</p>
  </article>
  <article class="project abs" style="left:436px;top:2062px;width:286px;height:229px;background:linear-gradient(160deg,#4f6a3a,#6d6a36 50%,#3a3a2a)" role="img" aria-label="Excavator digging beside green trees">
    <h3 class="wide">Lorem ipsum dolor amet</h3>
    <p>Duis autem vel eum iriure dolor in hendrerit in vulputate velit esse mole.</p>
  </article>
  <article class="project abs" style="left:733px;top:2062px;width:325px;height:156px;background:linear-gradient(180deg,#9aa5ad,#6a6a5a 55%,#7a5a38)" role="img" aria-label="Excavator near a farmhouse in autumn hills">
    <h3 class="wide">Lorem ipsum dolor sit amet,</h3>
    <p>Duis autem vel eum iriure dolor in hendrerit in vulputate velit esse molestie consequat.</p>
  </article>
  <article class="project abs" style="left:733px;top:2230px;width:325px;height:241px;background:linear-gradient(160deg,#c9b89a,#d69a44 40%,#5a4430)" role="img" aria-label="Excavator silhouetted against the setting sun">
    <h3 class="wide">Lorem ipsum dolor sit amet,</h3>
    <p>Duis autem vel eum iriure dolor in hendrerit in vulputate velit esse molestie consequat.</p>
  </article>
  <article class="project abs" style="left:141px;top:2301px;width:581px;height:170px;background:linear-gradient(100deg,#6f7a5c,#4f6a3a 40%,#5b5a55 70%,#3a3a3a);padding-left:394px;padding-right:16px" role="img" aria-label="Aerial view of roadworks in a suburban street">
    <h3 class="wide">Lorem ipsum<br>dolor sit amet,</h3>
    <p>Duis autem vel eum iriure dolor in hendrerit in vulputate velit esse molestie consequat.</p>
  </article>
</section>

<section class="quote">
  <div class="quote-bg abs" role="img" aria-label="Dark earthworks site in the background"></div>
  <svg class="abs" style="left:0;top:2985px" width="1200" height="130" viewBox="0 0 1200 130">
    <polygon points="0,35 210,25 210,75 0,110" fill="#c6cf2e"/>
    <polygon points="990,0 1200,-30 1200,130 990,130" fill="#fff"/>
    <polygon points="990,12 1200,30 1200,60 990,30" fill="#161616"/>
    <polygon points="0,110 210,75 210,130 0,130" fill="#fff"/>
  </svg>
  <div class="quote-head abs">
    <div class="eyebrow">QUICK INQUIRY</div>
    <h2 class="wide">REQUEST A QUOTE</h2>
    <p>Ready to move earth? Contact our Perth team for a no-obligation<br>site assessment and quote.</p>
  </div>
  <div class="quote-card abs">
    <div class="quote-form">
      <div class="field">First name*</div>
      <div class="field">Last name*</div>
      <div class="field">Your phone*</div>
      <div class="field">Your email*</div>
      <div class="field full">Message</div>
      <a class="btn btn-dark">SUBMIT NOW</a>
    </div>
    <div class="contact-info">
      <h3 class="wide">CONTACT<br>INFORMATION</h3>
      <div class="info-row"><svg viewBox="0 0 26 26" fill="#161616"><path d="M13 2a8 8 0 0 1 8 8c0 6-8 14-8 14S5 16 5 10a8 8 0 0 1 8-8zm0 5a3 3 0 1 0 0 6 3 3 0 0 0 0-6z"/></svg><span>123, Building Name, Street<br>City, State XY 123456</span></div>
      <div class="info-row"><svg viewBox="0 0 26 26" fill="none" stroke="#161616" stroke-width="2"><path d="M6 3h5l2 6-3 2a13 13 0 0 0 5 5l2-3 6 2v5c0 2-2 3-3 3C11 23 3 15 3 6c0-2 1-3 3-3z"/></svg><span>PHONE<br>(123) 456 7890</span></div>
      <div class="info-row"><svg viewBox="0 0 26 26" fill="none" stroke="#161616" stroke-width="2"><rect x="2" y="6" width="22" height="15"/><path d="M2 6l11 9 11-9"/></svg><span>EMAIL<br>info@bluegumridge.com</span></div>
      <div class="socials"><span></span><span></span><span></span><span></span></div>
    </div>
  </div>
</section>

<section class="newsletter">
  <div class="news-art abs" role="img" aria-label="Envelope with a letter illustration"></div>
  <h2 class="news-title wide abs">SUBSCRIBE TO OUR NEWSLETTER</h2>
  <p class="news-copy abs">Want to keep up to date with all our latest news and information?<br>Enter your email below to be added to our mailing list.</p>
  <div class="news-form abs"><span>Enter your email address</span><strong>SUBSCRIBE</strong></div>
</section>

<footer>
  <div class="footer-rule abs"></div>
  <div class="footer-brand abs">
    <div class="brand"><span class="brand-mark"></span><span class="brand-name" style="font-size:19px">Bluegum Ridge<br>Earthworks</span></div>
  </div>
  <nav class="footer-nav abs"><span class="active">HOME</span><span>ABOUT US</span><span>SERVICES</span><span>PROJECTS</span><span>CONTACT US</span></nav>
  <div class="footer-bottom abs"></div>
  <div class="footer-bar abs">
    <div class="info-row"><svg viewBox="0 0 26 26" fill="#161616"><path d="M13 2a8 8 0 0 1 8 8c0 6-8 14-8 14S5 16 5 10a8 8 0 0 1 8-8zm0 5a3 3 0 1 0 0 6 3 3 0 0 0 0-6z"/></svg><span>123, Building Name, Street<br>City, State XY 123456</span></div>
    <div class="info-row"><svg viewBox="0 0 26 26" fill="none" stroke="#161616" stroke-width="2"><path d="M6 3h5l2 6-3 2a13 13 0 0 0 5 5l2-3 6 2v5c0 2-2 3-3 3C11 23 3 15 3 6c0-2 1-3 3-3z"/></svg><span>PHONE<br>(123) 456 7890</span></div>
    <div class="info-row"><svg viewBox="0 0 26 26" fill="none" stroke="#161616" stroke-width="2"><rect x="2" y="6" width="22" height="15"/><path d="M2 6l11 9 11-9"/></svg><span>EMAIL<br>info@bluegumridge.com</span></div>
  </div>
  <div class="footer-digger abs" role="img" aria-label="Orange excavator illustration"></div>
  <p class="copyright abs">© 2026 Bluegum Ridge Earthworks. All Rights Reserved.</p>
  <div class="footer-social abs"><span></span><span></span><span></span><span></span></div>
</footer>

</body>
</html>
```